business card - for laser marking

I need design (curve) for my business card (make with laser) size 85mm x 55mm. How it look business card with laser marking see attached picture.

color:
Background: white
text and icons black

Please include: one side
1. dominik vrabec - direktor
2. phone: +386(0)41 726 190
+386(0)580 237 61
3. info@zarezko.example
4. faecebook.com/Zarezko.Ex
5. KM-ATELJE, Dominik Vrabec s.p.
Lipova ulica 19, 1000 Ljubljana, SI
6. logo

Please include: second side
1. logo
2. www.zarezko.example
3. Lasersko graviranje
ovitki telefonov, ohišja telefonov / tablic, nakit, ure, alu vizitke, dog-tagi, kemični svinčniki, orodja, noži, vžigalniki

Industry/Entity Type

Business

Contact Information for Business Card

Please include: one side
+386(0)580 237 61
3. info@zarezko.example
6. logo

1. logo
2. www.zarezko.example
3. Lasersko graviranje

Colors
000000
ffffff

Requirements
Must have
• I need design (curve) for my business card (make with laser) size 85mm x 55mm. How it look business card with laser marking see attached picture.
• color:
• Background: white
• text and icons black
• Please include: one side
• 1. dominik vrabec - direktor
• 2. phone: +386(0)41 726 190
• +386(0)580 237 61
• 3. info@zarezko.example
• 4. faecebook.com/Zarezko.Ex
• 5. KM-ATELJE, Dominik Vrabec s.p.
• Lipova ulica 19, 1000 Ljubljana, SI
• 6. logo
• Please include: second side
• 1. logo
• 2. www.zarezko.example
• 3. Lasersko graviranje
• ovitki telefonov, ohišja telefonov / tablic, nakit, ure, alu vizitke, dog-tagi, kemični svinčniki, orodja, noži, vžigalniki

```html
<!DOCTYPE html>
<html lang="sl">
<head>
<meta charset="utf-8">
<title>Zarezko – vizitka</title>
<link href="https://fonts.googleapis.com/css2?family=Roboto:wght@400;500;700&family=Roboto+Condensed:wght@700&display=swap" rel="stylesheet">
<style>
  :root {
    --backdrop: #e6e6e6;
    --card: #ffffff;
    --ink: #000000;
    --ink-soft: #1a1a1a;
    --splash-dark: #000000;
    --splash-mid: #555555;
  }
  * { margin: 0; padding: 0; box-sizing: border-box; }
  html, body {
    width: 1200px; height: 960px; overflow: hidden;
    background: var(--backdrop);
    font-family: "Roboto", Arial, sans-serif;
  }
  .card {
    position: absolute;
    width: 600px; height: 342px;
    border-radius: 16px;
    overflow: hidden;
    background: var(--card);
    color: var(--ink);
  }

  /* Front side */
  .card--front {
    left: 322px; top: 108px;
    text-align: center;
  }
  .brand {
    position: absolute; left: 0; right: 0; top: 130px;
    display: flex; justify-content: center; align-items: center; gap: 10px;
  }
  .brand__dot {
    width: 12px; height: 12px; border-radius: 50%;
    background: var(--ink);
  }
  .brand__name {
    font-weight: 700; font-size: 26px; letter-spacing: 1px;
    color: var(--ink);
  }
  .services {
    position: absolute; left: 0; right: 0; top: 240px;
    font-size: 14.5px; line-height: 18px;
  }
  .website {
    position: absolute; left: 0; right: 0; top: 301px;
    font-size: 16.5px; font-weight: 500;
  }

  /* Back side */
  .card--back {
    left: 320px; top: 493px;
  }
  .splash-area {
    position: absolute; left: 0; top: 0;
    width: 330px; height: 250px;
    background: linear-gradient(165deg, var(--splash-dark) 0%, var(--splash-mid) 55%, rgba(0,0,0,0) 100%);
    border-bottom-right-radius: 120px;
  }
  .identity {
    position: absolute; right: 36px; top: 44px; text-align: right;
  }
  .identity__name {
    font-family: "Roboto Condensed", "Arial Narrow", sans-serif;
    font-weight: 700; font-size: 21px; letter-spacing: .3px;
  }
  .identity__role {
    font-weight: 500; font-size: 14px;
    margin-top: 4px; letter-spacing: .3px;
  }
  .address {
    position: absolute; right: 36px; top: 148px;
    text-align: right; font-size: 14.5px; line-height: 18px;
    font-style: normal; color: var(--ink-soft);
  }
  .contacts {
    position: absolute; right: 36px; top: 226px;
    list-style: none; text-align: right;
    font-size: 14.5px; line-height: 19px; color: var(--ink-soft);
  }
  .contacts li {
    display: flex; justify-content: flex-end; align-items: center; gap: 8px;
  }
  .contacts svg { width: 13px; height: 13px; fill: var(--ink); flex: none; }
</style>
</head>
<body>

<section class="card card--front">
  <div class="brand">
    <span class="brand__dot"></span>
    <span class="brand__name">ZAREZKO</span>
  </div>
  <p class="services">
    Lasersko graviranje<br>
    ovitki telefonov, ohišja telefonov / tablic, nakit, ure, alu vizitke<br>
    dog-tagi, kemicni svincniki, orodja, noži, vžigalniki
  </p>
  <p class="website">www.zarezko.example</p>
</section>

<section class="card card--back">
  <div class="splash-area" role="img" aria-label="Engraved paint splash decoration"></div>

  <div class="identity">
    <h1 class="identity__name">DOMINIK VRABEC</h1>
    <p class="identity__role">DIREKTOR</p>
  </div>

  <address class="address">
    KM-ATELJE<br>
    Dominik Vrabec s.p.<br>
    Lipova ulica 19<br>
    1000 Ljubljana, SI
  </address>

  <ul class="contacts">
    <li>+386(0)580 237 61
      <svg viewBox="0 0 24 24" aria-hidden="true"><path d="M6.6 10.8a15 15 0 0 0 6.6 6.6l2.2-2.2c.3-.3.7-.4 1-.2 1.1.4 2.3.6 3.6.6.6 0 1 .4 1 1V20c0 .6-.4 1-1 1A17 17 0 0 1 3 4c0-.6.4-1 1-1h3.5c.6 0 1 .4 1 1 0 1.3.2 2.5.6 3.6.1.3 0 .7-.2 1z"/></svg>
    </li>
    <li>+386(0)41 726 190
      <svg viewBox="0 0 24 24" aria-hidden="true"><path d="M7 1h10a2 2 0 0 1 2 2v18a2 2 0 0 1-2 2H7a2 2 0 0 1-2-2V3a2 2 0 0 1 2-2zm0 3v14h10V4zm5 15.2a1.2 1.2 0 1 0 0 2.4 1.2 1.2 0 0 0 0-2.4z"/></svg>
    </li>
    <li>info@zarezko.example
      <svg viewBox="0 0 24 24" aria-hidden="true"><path d="M2 5h20v14H2zm2 2v.5l8 5 8-5V7l-8 5z"/></svg>
    </li>
    <li>Zarezko.Ex
      <svg viewBox="0 0 24 24" aria-hidden="true"><rect x="2" y="2" width="20" height="20" rx="2"/></svg>
    </li>
  </ul>
</section>

</body>
</html>
```